Roadside building business signage for a holistic health clinic.

Replace signs as shown in the attached file. They are perforated stickers that go on the windows as shown. Looking for something that has our logo and says the name of the practice with logo (Fernridge Health & Wellness) also boldly says Acupuncture, IV Vitamins, and Holistic Health.
Possibly our phone number as well 318-562-7041
Updates

Please don't use pink except the logo. Earthy, organic tone colors appreciated.

Need of eye catching window signage of a holistic clinic on a brick building. Pink, purple, sage green, white color. Logo is pink on a white background. Please don't overload with too much pink. Words to include are "Fernridge Health and Wellness(name of business)", "Direct Primary Care", " Medical acupuncture", "IV Vitamin Therapy", "fernridgecareclinic.example","318-562-7041".

Target Market(s)

People will see in their cars passing by the building. Busy roadside so need to be visible while passing in fast speed.

Industry/Entity Type

Health & Wellness

Font styles to use
Sans Serif

Colors

Designer to choose colors to be used in the design.

Requirements
Must have
• On sign must have words Holistic Medicine, Medical Acupuncture, Direct Primary Care and IV vitamins.
Nice to have
• Simple, minimalistic, artistic yet has clear message. White, Black, Violet, Pink (logo), Dark green, Sage green.
Should not have
• Bold colors (red, yellow, blue), same tone colors. Blue waves on the current signage (uploaded file) must go.

```html
<!DOCTYPE html>
<html lang="en">
<head>
<meta charset="utf-8">
<title>Fernridge Health &amp; Wellness – Window Signage Panels</title>
<link href="https://fonts.googleapis.com/css2?family=Montserrat:wght@400;500;600;700&display=swap" rel="stylesheet">
<style>
  :root {
    --page: #e9e9ea;
    --cream: #fbf6ea;
    --cream-deep: #efe3c6;
    --sage: #5f8a73;
    --sage-light: #7a9e8a;
    --forest: #1f4a3a;
    --maroon: #6b2342;
    --mauve: #cbbcc4;
    --ink: #222222;
    --rule: #c9c2bb;
    --pink: #e0508f;
  }
  * { box-sizing: border-box; margin: 0; padding: 0; }
  html, body {
    width: 1200px; height: 2934px; overflow: hidden;
    background: var(--page);
    font-family: "Montserrat", sans-serif;
  }
  .sheet { position: relative; width: 1200px; height: 2934px; }

  .panel {
    position: absolute; width: 500px; height: 500px; overflow: hidden;
    background: radial-gradient(circle at 30% 25%, var(--cream) 0%, var(--cream-deep) 55%, var(--cream) 100%);
    box-shadow: 0 2px 6px rgba(0,0,0,.12);
  }
  .panel svg.shapes { position: absolute; inset: 0; }
  .base-band { position: absolute; left: 0; bottom: 0; width: 100%; height: 14px; background: var(--sage); }

  .col-left { left: 70px; }
  .col-right { left: 630px; }
  .row-1 { top: 920px; }
  .row-2 { top: 1511px; }
  .row-3 { top: 2086px; }

  .arch-piece { position: absolute; left: 425px; top: 348px; width: 494px; height: 500px;
    filter: drop-shadow(0 2px 4px rgba(0,0,0,.12)); }

  /* wordmark */
  .wordmark { position: absolute; left: 0; width: 100%; text-align: center; color: var(--forest); font-weight: 600; }
  .wordmark .mark-dot { display: block; margin: 0 auto 14px; border-radius: 50%; background: var(--pink); }
  .wordmark .name { display: block; letter-spacing: .12em; line-height: 1; }
  .wordmark .tagline { display: block; letter-spacing: .42em; margin-top: 8px; }
  .wordmark--large { top: 140px; }
  .wordmark--large .mark-dot { width: 70px; height: 70px; }
  .wordmark--large .name { font-size: 56px; }
  .wordmark--large .tagline { font-size: 15px; }
  .wordmark--medium { top: 235px; }
  .wordmark--medium .mark-dot { width: 56px; height: 56px; }
  .wordmark--medium .name { font-size: 44px; }
  .wordmark--medium .tagline { font-size: 12px; }
  .wordmark--faint { top: 70px; color: var(--sage-light); }
  .wordmark--faint .name { font-size: 38px; }
  .wordmark--faint .tagline { font-size: 10px; }

  /* services */
  .foliage { position: absolute; left: 0; top: 0; width: 135px; height: 176px;
    background: radial-gradient(ellipse at 35% 35%, #a9bfa0 0%, #c9d6bd 55%, rgba(233,226,205,0) 100%); }
  .service { position: absolute; font-weight: 700; font-size: 30px; color: var(--ink); line-height: 1; }
  .service--acupuncture { left: 242px; top: 91px; }
  .service--iv { left: 46px; top: 203px; }
  .service--holistic { left: 240px; top: 312px; }
  .contact-bar { position: absolute; left: 0; bottom: 0; width: 100%; height: 71px; background: var(--sage);
    border-top: 4px solid var(--maroon); display: flex; align-items: center; gap: 14px; padding-left: 18px; color: #fff; font-weight: 700; }
  .contact-bar .phone { font-size: 23px; display: flex; align-items: center; gap: 6px; }
  .contact-bar .web { font-size: 15px; font-weight: 600; display: flex; align-items: center; gap: 5px; }

  /* direct primary care */
  .dpc-title { position: absolute; left: 0; top: 108px; width: 100%; text-align: center; font-weight: 700; line-height: 1.05; }
  .dpc-title .lead { display: block; font-size: 48px; color: var(--ink); }
  .dpc-title .accent { display: block; font-size: 50px; color: var(--maroon); letter-spacing: .02em; }
  .dpc-rule { position: absolute; left: 29px; top: 241px; width: 442px; height: 1px; background: var(--rule); }
  .dpc-rule-accent { position: absolute; left: 216px; top: 238px; width: 68px; height: 6px; border-radius: 3px; background: var(--sage); }
  .dpc-phone-icon { position: absolute; left: 221px; top: 286px; width: 58px; height: 58px; }
  .dpc-number { position: absolute; left: 0; top: 358px; width: 100%; text-align: center; font-size: 40px; font-weight: 700; color: var(--ink); letter-spacing: .03em; }
</style>
</head>
<body>
<main class="sheet">

  <!-- arch top piece -->
  <svg class="arch-piece" viewBox="0 0 494 500" aria-label="Arched window piece">
    <defs>
      <clipPath id="arch-clip"><path d="M0 0 H40 C250 10 430 200 494 500 H0 Z"/></clipPath>
      <radialGradient id="cream-wash" cx="40%" cy="35%" r="75%">
        <stop offset="0" stop-color="#fbf6ea"/><stop offset=".55" stop-color="#efe3c6"/><stop offset="1" stop-color="#fbf6ea"/>
      </radialGradient>
    </defs>
    <g clip-path="url(#arch-clip)">
      <rect width="494" height="500" fill="url(#cream-wash)"/>
      <path d="M0 0 V290 C50 250 110 265 160 245 C210 225 170 140 205 90 C225 60 235 52 260 48 V0 Z" fill="var(--sage)"/>
      <path d="M0 300 C55 262 115 277 168 255 C222 232 182 146 215 98 C232 72 245 62 270 58" fill="none" stroke="var(--mauve)" stroke-width="14"/>
    </g>
  </svg>

  <!-- logo panel -->
  <section class="panel col-left row-1">
    <div class="wordmark wordmark--large">
      <span class="mark-dot"></span>
      <span class="name">FERNRIDGE</span>
      <span class="tagline">HEALTH &amp; WELLNESS</span>
    </div>
  </section>

  <!-- services panel -->
  <section class="panel col-right row-1">
    <div class="foliage" role="img" aria-label="Eucalyptus leaves sprig"></div>
    <svg class="shapes" viewBox="0 0 500 500" width="500" height="500">
      <g fill="none" stroke="var(--maroon)" stroke-width="1.5">
        <path d="M500 56 H232 L206 107 L232 160 H500"/>
        <path d="M0 165 H250 L276 219 L250 272 H0"/>
        <path d="M500 273 H232 L206 328 L232 383 H500"/>
      </g>
      <g stroke="var(--rule)" stroke-width="1">
        <line x1="0" y1="163" x2="500" y2="163"/>
        <line x1="0" y1="275" x2="500" y2="275"/>
      </g>
      <polygon points="181,65 217,86 217,128 181,149 145,128 145,86" fill="var(--sage)"/>
      <polygon points="181,74 209,90 209,124 181,140 153,124 153,90" fill="none" stroke="#fff" stroke-width="1.5" stroke-dasharray="4 3"/>
      <polygon points="294,177 330,198 330,240 294,261 258,240 258,198" fill="var(--maroon)"/>
      <polygon points="294,186 322,202 322,236 294,252 266,236 266,202" fill="none" stroke="#fff" stroke-width="1.5" stroke-dasharray="4 3"/>
      <polygon points="181,286 217,307 217,349 181,370 145,349 145,307" fill="var(--sage)"/>
      <polygon points="181,295 209,311 209,345 181,361 153,345 153,311" fill="none" stroke="#fff" stroke-width="1.5" stroke-dasharray="4 3"/>
    </svg>
    <span class="service service--acupuncture">Acupuncture</span>
    <span class="service service--iv">IV Vitamins</span>
    <span class="service service--holistic">Holistic Health</span>
    <div class="contact-bar">
      <span class="phone">
        <svg width="18" height="18" viewBox="0 0 24 24"><path d="M6.6 10.8a15 15 0 0 0 6.6 6.6l2.2-2.2a1 1 0 0 1 1-.25 11.4 11.4 0 0 0 3.6.57 1 1 0 0 1 1 1V20a1 1 0 0 1-1 1A17 17 0 0 1 3 4a1 1 0 0 1 1-1h3.5a1 1 0 0 1 1 1c0 1.25.2 2.45.57 3.57a1 1 0 0 1-.25 1z" fill="#fff"/></svg>
        318-562-7041
      </span>
      <span class="web">
        <svg width="15" height="15" viewBox="0 0 24 24" fill="none" stroke="#fff" stroke-width="2"><circle cx="12" cy="12" r="10"/><path d="M2 12h20M12 2c3 3 3 17 0 20M12 2c-3 3-3 17 0 20"/></svg>
        fernridgecareclinic.example
      </span>
    </div>
  </section>

  <!-- wave logo panel, green right -->
  <section class="panel col-left row-2">
    <svg class="shapes" viewBox="0 0 500 500" width="500" height="500">
      <path d="M186 0 C250 0 235 80 270 150 C300 200 380 190 500 235 V0 Z" fill="var(--sage)"/>
      <path d="M178 0 C242 2 226 84 262 156 C294 210 378 200 500 246" fill="none" stroke="var(--mauve)" stroke-width="14"/>
    </svg>
    <div class="wordmark wordmark--medium">
      <span class="mark-dot"></span>
      <span class="name">FERNRIDGE</span>
      <span class="tagline">HEALTH &amp; WELLNESS</span>
    </div>
    <div class="base-band"></div>
  </section>

  <!-- wave logo panel, green left -->
  <section class="panel col-right row-2">
    <svg class="shapes" viewBox="0 0 500 500" width="500" height="500">
      <path d="M314 0 C250 0 265 80 230 150 C200 200 120 190 0 235 V0 Z" fill="var(--sage)"/>
      <path d="M322 0 C258 2 274 84 238 156 C206 210 122 200 0 246" fill="none" stroke="var(--mauve)" stroke-width="14"/>
    </svg>
    <div class="wordmark wordmark--medium">
      <span class="mark-dot"></span>
      <span class="name">FERNRIDGE</span>
      <span class="tagline">HEALTH &amp; WELLNESS</span>
    </div>
    <div class="base-band"></div>
  </section>

  <!-- direct primary care panel -->
  <section class="panel col-left row-3">
    <h2 class="dpc-title"><span class="lead">DIRECT</span><span class="accent">PRIMARY CARE</span></h2>
    <div class="dpc-rule"></div>
    <div class="dpc-rule-accent"></div>
    <svg class="dpc-phone-icon" viewBox="0 0 58 58">
      <circle cx="29" cy="29" r="26" fill="none" stroke="var(--maroon)" stroke-width="3"/>
      <circle cx="29" cy="29" r="20" fill="var(--maroon)"/>
      <path transform="translate(19 19) scale(.85)" d="M6.6 10.8a15 15 0 0 0 6.6 6.6l2.2-2.2a1 1 0 0 1 1-.25 11.4 11.4 0 0 0 3.6.57 1 1 0 0 1 1 1V20a1 1 0 0 1-1 1A17 17 0 0 1 3 4a1 1 0 0 1 1-1h3.5a1 1 0 0 1 1 1c0 1.25.2 2.45.57 3.57a1 1 0 0 1-.25 1z" fill="#fff"/>
    </svg>
    <p class="dpc-number">318-562-7041</p>
    <div class="base-band"></div>
  </section>

  <!-- green wave panel -->
  <section class="panel col-right row-3">
    <svg class="shapes" viewBox="0 0 500 500" width="500" height="500">
      <path d="M0 365 C60 330 100 310 149 285 C200 255 220 215 277 181 C330 150 380 115 437 85 C470 65 490 40 500 10 V0 H0 Z" fill="var(--sage)"/>
      <path d="M0 377 C62 342 102 322 152 297 C204 267 224 227 281 193 C334 162 384 127 441 97 C474 77 494 52 504 22" fill="none" stroke="var(--mauve)" stroke-width="14"/>
    </svg>
    <div class="wordmark wordmark--faint">
      <span class="name">FERNRIDGE</span>
      <span class="tagline">HEALTH &amp; WELLNESS</span>
    </div>
    <div class="base-band"></div>
  </section>

</main>
</body>
</html>
```